Business Card Design

Business Card for professional consulting firm working with large financial institutions.

Target Market(s)

Executive buyers

Industry/Entity Type

Banking

Contact Information for Business Card

Mild creativity wanted. Not boring, but do elaborate artwork.

Font styles to use
Serif
Sans Serif

Colors

Designer to choose colors to be used in the design.

Requirements
Must have
• Standard business card features - company name, individual name, telephone, website, email, locations.
Nice to have
• Two colors
Should not have
• too many colors, fancy printing, cartoons.

```html
<!DOCTYPE html>
<html lang="en">
<head>
<meta charset="utf-8">
<title>Norvale Partners Business Card</title>
<link rel="stylesheet" href="https://fonts.googleapis.com/css2?family=Merriweather:wght@300;400;700&family=Open+Sans:wght@400;600&display=swap">
<style>
  :root {
    --canvas: #e9e9ea;
    --ink-mid: #474747;
    --band-dark: #333333;
    --band-light: #5a5a5a;
    --arc-grey: #b5b5b5;
    --arc-soft: #d2d2d2;
    --paper: #f7f7f7;
    --text-grey: #5b5b5b;
    --white: #ffffff;
  }
  * { box-sizing: border-box; margin: 0; padding: 0; }
  html, body {
    width: 1200px; height: 726px; overflow: hidden;
    background: var(--canvas);
  }
  .stage {
    position: relative; width: 1200px; height: 726px;
    display: flex; align-items: center; justify-content: center; gap: 44px;
  }
  .card {
    position: relative; width: 520px; height: 300px; overflow: hidden;
    box-shadow: 0 6px 18px rgba(0,0,0,0.18);
  }
  .card-back {
    background: linear-gradient(160deg, var(--band-light) 0%, var(--band-dark) 55%, #262626 100%);
    display: flex; align-items: center; justify-content: center;
  }
  .brand {
    font-family: "Merriweather", Georgia, serif;
    font-weight: 400; letter-spacing: 0.5px; white-space: nowrap; line-height: 1.2;
  }
  .card-back .brand { font-size: 40px; color: var(--white); }
  .card-front { background: var(--paper); }
  .front-art { position: absolute; inset: 0; }
  .front-art svg { display: block; }
  .holder {
    position: absolute; right: 26px; top: 22px; text-align: right; color: var(--white);
  }
  .holder-name { font-family: "Open Sans", Arial, sans-serif; font-weight: 600; font-size: 19px; }
  .holder-title { font-family: "Merriweather", Georgia, serif; font-weight: 300; font-size: 11px; margin-top: 3px; color: #e6e6e6; }
  .card-front .brand {
    position: absolute; left: 40px; top: 162px; font-size: 30px; color: var(--ink-mid);
  }
  .contacts {
    position: absolute; right: 24px; top: 150px; list-style: none; text-align: right;
    font-family: "Merriweather", Georgia, serif; font-weight: 300; font-size: 12.5px; color: var(--text-grey);
  }
  .contacts li { display: flex; align-items: center; justify-content: flex-end; gap: 8px; line-height: 21px; }
  .contacts svg { width: 11px; height: 11px; fill: var(--ink-mid); }
  .address {
    position: absolute; left: 34px; bottom: 24px;
    font-family: "Merriweather", Georgia, serif; font-weight: 300; font-size: 13px; line-height: 21px; color: var(--text-grey);
  }
</style>
</head>
<body>
<main class="stage">
  <section class="card card-back" aria-label="Card back">
    <span class="brand">norvale partners</span>
  </section>

  <section class="card card-front" aria-label="Card front">
    <div class="front-art">
      <svg width="520" height="300" viewBox="0 0 520 300" aria-hidden="true">
        <defs>
          <linearGradient id="band" x1="0" y1="0" x2="1" y2="0">
            <stop offset="0" stop-color="#1f1f1f"/>
            <stop offset="1" stop-color="#5c5c5c"/>
          </linearGradient>
        </defs>
        <path d="M0 136 C90 112 200 125 300 122 C390 118 450 106 520 112 L520 124 C450 120 390 132 300 136 C200 140 90 130 0 150 Z" fill="var(--arc-soft)"/>
        <path d="M0 112 C90 90 200 105 300 100 C390 95 450 84 520 90 L520 104 C450 98 390 112 300 116 C200 120 90 106 0 128 Z" fill="var(--arc-grey)"/>
        <path d="M0 0 H520 V80 C450 72 390 85 300 90 C200 96 90 80 0 105 Z" fill="url(#band)"/>
      </svg>
    </div>

    <div class="holder">
      <div class="holder-name">John Doe Smith</div>
      <div class="holder-title">Managing Director</div>
    </div>

    <span class="brand">norvale partners</span>

    <ul class="contacts">
      <li>555.555.5555
        <svg viewBox="0 0 24 24" aria-hidden="true"><path d="M6.6 10.8a15 15 0 0 0 6.6 6.6l2.2-2.2a1 1 0 0 1 1-.25 11.4 11.4 0 0 0 3.6.57 1 1 0 0 1 1 1V20a1 1 0 0 1-1 1A17 17 0 0 1 3 4a1 1 0 0 1 1-1h3.5a1 1 0 0 1 1 1c0 1.25.2 2.45.57 3.6a1 1 0 0 1-.25 1z"/></svg>
      </li>
      <li>yourwebsite.com
        <svg viewBox="0 0 24 24" aria-hidden="true"><path d="M2 5h20v14H2z M2 5l10 8 10-8" fill="none" stroke="#474747" stroke-width="2.4"/></svg>
      </li>
      <li>johndoe@example.com
        <svg viewBox="0 0 24 24" aria-hidden="true"><circle cx="12" cy="12" r="9.5" fill="none" stroke="#474747" stroke-width="2.2"/><path d="M2.5 12h19M12 2.5c3 3 3 16 0 19M12 2.5c-3 3-3 16 0 19" fill="none" stroke="#474747" stroke-width="1.8"/></svg>
      </li>
    </ul>

    <p class="address">234 Anywhere St., Any City,<br>Any Town, US 123456</p>
  </section>
</main>
</body>
</html>
```